Investment company needing business card

We are wanting a business card which looks sharp and easy on the eye. We are thinking of having a business card with the logo embossed on it, to really make it stand out. We will only have a small amount of information of the business card, person's name, position, email address and phone number

Contact Information for Business Card

Danielle Frost
Executive Assistant
+64 21 473 5162
danielf@harwickpartners.co.nz

Requirements
Must have
• Embossed logo
Should not have
• Not to be busy

```html
<!DOCTYPE html>
<html lang="en">
<head>
<meta charset="utf-8">
<title>Harwick Partners — Business Card</title>
<link rel="stylesheet" href="https://fonts.googleapis.com/css2?family=Roboto:ital,wght@0,400;0,700;1,700&display=swap">
<style>
  :root {
    --backdrop: #8e8a88;
    --card: #f4f4f1;
    --brand-green: #1f9a52;
    --ink-grey: #4f5052;
    --text-grey: #5c5d5f;
  }
  html, body {
    margin: 0;
    padding: 0;
    width: 1200px;
    height: 778px;
    overflow: hidden;
    background: var(--backdrop);
  }
  .canvas {
    position: relative;
    width: 1200px;
    height: 778px;
    display: flex;
    align-items: center;
    justify-content: center;
  }
  .business-card {
    position: relative;
    width: 900px;
    height: 500px;
    background: var(--card);
    box-sizing: border-box;
    border-bottom: 6px solid var(--brand-green);
  }
  .brand {
    position: absolute;
    left: 64px;
    top: 62px;
    display: flex;
    align-items: center;
    gap: 14px;
  }
  .brand-square {
    width: 40px;
    height: 40px;
    background: var(--brand-green);
  }
  .brand-name {
    font-family: "Roboto", Arial, sans-serif;
    font-weight: 700;
    font-size: 30px;
    letter-spacing: 1px;
    text-transform: uppercase;
    color: var(--brand-green);
  }
  .contact-block {
    position: absolute;
    right: 56px;
    top: 278px;
    width: 390px;
  }
  .person-name {
    font-family: "Roboto", Arial, sans-serif;
    font-style: italic;
    font-weight: 700;
    font-size: 26px;
    letter-spacing: 0.5px;
    text-transform: uppercase;
    color: var(--brand-green);
    margin: 0;
    line-height: 1.1;
  }
  .person-role {
    font-family: "Roboto", Arial, sans-serif;
    font-style: italic;
    font-weight: 700;
    font-size: 20px;
    letter-spacing: 0.5px;
    text-transform: uppercase;
    color: var(--ink-grey);
    margin: 4px 0 0;
  }
  .divider {
    display: block;
    margin: 10px 0 14px;
  }
  .contact-lines {
    list-style: none;
    margin: 0;
    padding: 0;
    font-family: "Roboto", Arial, sans-serif;
    font-weight: 400;
    font-size: 18px;
    line-height: 1.45;
    letter-spacing: 0.4px;
    color: var(--text-grey);
  }
</style>
</head>
<body>
  <main class="canvas">
    <section class="business-card" aria-label="Business card">
      <div class="brand">
        <span class="brand-square" aria-hidden="true"></span>
        <span class="brand-name">Harwick Partners</span>
      </div>

      <div class="contact-block">
        <h1 class="person-name">Danielle Frost</h1>
        <p class="person-role">Executive Assistant</p>
        <svg class="divider" width="390" height="2" viewBox="0 0 390 2" aria-hidden="true">
          <line x1="0" y1="1" x2="390" y2="1" stroke="var(--brand-green)" stroke-width="1.5"/>
        </svg>
        <ul class="contact-lines">
          <li>+64 21 473 5162</li>
          <li>danielf@harwickpartners.co.nz</li>
          <li>www.harwickpartners.co.nz</li>
        </ul>
      </div>
    </section>
  </main>
</body>
</html>
```